I need a business card design for a new business based in South West Australia.
I specialize in residential window cleaning & general handyman maintenance.

Dale Marsh - 412 SILVER HAWK DETAILING
- Window Cleaning
- House Maintenance

```html
<!DOCTYPE html>
<html lang="en">
<head>
<meta charset="utf-8">
<title>Silver Hawk Detailing – Business Card</title>
<link rel="stylesheet" href="https://fonts.googleapis.com/css2?family=Arimo:wght@400;500&family=Playfair+Display:wght@600&display=swap">
<style>
  :root {
    --page-bg: #e9e7e3;
    --card-blue: #4a82c4;
    --card-white: #efefef;
    --band-black: #111111;
    --ink: #1a1a1a;
    --text-light: #ffffff;
    --tool-steel: #8a8f96;
  }
  html, body {
    margin: 0;
    padding: 0;
    width: 1200px;
    height: 902px;
    overflow: hidden;
    background: var(--page-bg);
  }
  .business-card {
    position: absolute;
    left: 75px;
    top: 151px;
    width: 1050px;
    height: 600px;
    overflow: hidden;
    background: var(--card-blue);
    box-shadow: 0 10px 30px rgba(0,0,0,0.18);
  }
  .card-shapes {
    position: absolute;
    inset: 0;
  }
  .company-name {
    position: absolute;
    left: 130px;
    top: 170px;
    margin: 0;
    font-family: "Arimo", sans-serif;
    font-weight: 500;
    font-size: 42px;
    letter-spacing: 0.5px;
    color: var(--ink);
    white-space: nowrap;
  }
  .tool-illustration {
    position: absolute;
    left: 910px;
    top: 60px;
    width: 115px;
    height: 150px;
  }
  .service-list {
    position: absolute;
    left: 640px;
    top: 370px;
    margin: 0;
    padding: 0;
    list-style: none;
    font-family: "Arimo", sans-serif;
    font-size: 32px;
    color: var(--text-light);
  }
  .service-list li {
    display: flex;
    align-items: center;
    gap: 22px;
    margin-bottom: 26px;
  }
  .service-icon {
    width: 22px;
    height: 22px;
    flex: none;
  }
  .owner-name {
    position: absolute;
    left: 70px;
    top: 490px;
    margin: 0;
    font-family: "Playfair Display", serif;
    font-weight: 600;
    font-size: 60px;
    color: var(--text-light);
    white-space: nowrap;
  }
</style>
</head>
<body>
  <article class="business-card">
    <svg class="card-shapes" viewBox="0 0 1050 600" width="1050" height="600" aria-hidden="true">
      <path class="curve-band" d="M0,300 C90,395 250,478 430,478 C680,478 850,320 900,0 H870 C820,300 660,440 430,440 C250,440 100,380 0,330 Z" fill="var(--band-black)"/>
      <path class="curve-white-edge" d="M0,330 C100,380 250,440 430,440 C660,440 820,300 870,0 H0 Z" fill="var(--card-white)" stroke="#ffffff" stroke-width="6"/>
      <path class="curve-white" d="M0,0 H870 C820,300 660,440 430,440 C250,440 100,380 0,330 Z" fill="var(--card-white)"/>
    </svg>

    <h1 class="company-name">412 SILVER HAWK DETAILING</h1>

    <svg class="tool-illustration" viewBox="0 0 115 150" role="img" aria-label="Window squeegee illustration">
      <rect x="0" y="0" width="115" height="150" rx="8" fill="var(--tool-steel)" opacity="0.55"/>
    </svg>

    <ul class="service-list">
      <li>
        <svg class="service-icon" viewBox="0 0 22 22" aria-hidden="true">
          <circle cx="11" cy="11" r="8" fill="none" stroke="#ffffff" stroke-width="1.5"/>
          <circle cx="11" cy="11" r="3" fill="#ffffff"/>
          <path d="M11 0v6M11 16v6M0 11h6M16 11h6" stroke="#ffffff" stroke-width="1.5"/>
        </svg>
        <span>Window Cleaning</span>
      </li>
      <li>
        <svg class="service-icon" viewBox="0 0 22 22" aria-hidden="true">
          <circle cx="11" cy="11" r="8" fill="none" stroke="#ffffff" stroke-width="1.5"/>
          <circle cx="11" cy="11" r="3" fill="#ffffff"/>
          <path d="M11 0v6M11 16v6M0 11h6M16 11h6" stroke="#ffffff" stroke-width="1.5"/>
        </svg>
        <span>House Maintenance</span>
      </li>
    </ul>

    <p class="owner-name">Dale Marsh</p>
  </article>
</body>
</html>
```